Phuket Thailand - Rental Villa Website

I have a villa for rent in Thailand and require a website - i need to demo pictures/walk through video, local attractions, villa facilities description plus seaonal rates and online booking.

Industry/Entity Type

Rental

Coding

Coded - Design and coding required

```html
<!DOCTYPE html>
<html lang="en">
<head>
<meta charset="utf-8">
<title>Villa Rental</title>
<link rel="stylesheet" href="https://fonts.googleapis.com/css2?family=Roboto:wght@400;500;700&family=Open+Sans:wght@600;700&display=swap">
<style>
:root{
  --teal:#3aa6c0;
  --teal-dark:#2b8fa8;
  --panel:#4aa9bf;
  --blue-btn:#2577c4;
  --ink:#3b3b3b;
  --muted:#6a6a6a;
  --dark:#2b2827;
  --footer:#2a2a2a;
  --footer-text:#9a9a9a;
  --white:#ffffff;
  --price-red:#d9464a;
  --circle:#b9b9b9;
  --field-grey:#6b6b6b;
}
*{margin:0;padding:0;box-sizing:border-box}
html,body{width:1200px;height:2225px;overflow:hidden;background:var(--white)}
body{position:relative;font-family:"Roboto",Arial,sans-serif;color:var(--ink)}
.abs{position:absolute}

/* header */
.top-line{left:0;top:0;width:1200px;height:4px;background:var(--teal)}
.brand{left:98px;top:44px;display:flex;align-items:center;gap:12px}
.brand-mark{width:40px;height:40px;background:var(--teal)}
.brand-name{font-weight:700;font-size:24px;color:var(--ink);letter-spacing:.1px;white-space:nowrap}
.nav{right:98px;top:49px;display:flex;align-items:center;font-size:12px;font-weight:500;color:var(--ink);white-space:nowrap}
.nav a{color:inherit;text-decoration:none;height:31px;line-height:31px;padding:0 0 0 34px}
.nav a.active{background:var(--teal);color:var(--white);padding:0 19px;border-radius:2px;margin-right:-15px}
.nav a.active + a{padding-left:34px}

/* hero */
.hero{left:0;top:128px;width:1200px;height:510px;background:linear-gradient(100deg,#6d7279 0%,#a9a39a 35%,#c8c2b8 55%,#8b7b6a 80%,#6a4f4a 100%)}
.hero-caption{left:538px;top:308px;width:562px;height:101px;background:rgba(40,40,40,.78);padding:13px 22px 0;color:var(--white)}
.hero-caption h1{font-family:"Open Sans",Arial,sans-serif;font-weight:700;font-size:24px;line-height:28px;letter-spacing:.2px;white-space:nowrap}
.hero-caption p{font-size:12px;line-height:18px;margin-top:3px;color:#eee}
.hero-price{display:flex;align-items:baseline;gap:14px;margin-top:2px;line-height:20px}
.hero-price .amount{color:var(--teal);font-size:19px;font-weight:700}
.hero-price .more{font-size:12px;font-weight:700}
.dots{position:absolute;right:22px;bottom:14px;display:flex;gap:6px}
.dots i{width:7px;height:7px;border-radius:50%;background:var(--white)}
.dots i.on{background:var(--teal)}

/* search */
.search{left:98px;top:615px;width:1002px;height:270px;background:var(--panel)}
.search-title{left:0;width:1002px;top:22px;text-align:center;color:var(--white);font-weight:500;font-size:15.5px}
.search-rule{left:376px;top:45px}
.field{height:26px;background:var(--white);border-radius:2px;font-size:11px;color:#aaa;padding:0 9px;line-height:26px}
.field svg{position:absolute;right:8px;top:10px}
.btn-search{background:var(--field-grey);color:var(--white);text-align:center;font-size:11.5px;line-height:26px;height:26px;border-radius:2px}
.btn-book{left:433px;top:211px;width:139px;height:39px;background:linear-gradient(#3a8ee0,var(--blue-btn));color:var(--white);font-weight:700;font-size:13.5px;text-align:center;line-height:39px;border-radius:2px}

/* rates */
.section-title{width:1200px;left:0;text-align:center;font-size:22px;font-weight:400;color:var(--ink)}
.rate-line{left:139px;top:1022px;width:920px;height:1px;background:#d8d8d8}
.rate{width:83px;height:83px;border-radius:50%;background:var(--circle);border:2px solid #cfcfcf;color:var(--white);font-weight:700;font-size:18px;text-align:center;line-height:79px}
.rate-label{color:var(--teal);font-size:13.5px;font-weight:500;width:120px;text-align:center}

/* attractions */
.attractions{left:0;top:1143px;width:1200px;height:517px;background:var(--dark)}
.attractions .section-title{color:var(--white);top:24px}
.photo{border:3px solid var(--white)}
.card{background:var(--white);width:280px;height:136px;padding:16px 20px}
.card h3{font-size:15px;font-weight:500;color:var(--ink);white-space:nowrap}
.card p{font-size:10px;line-height:19px;color:var(--muted);margin-top:4px}
.card .price{color:var(--price-red);font-size:18px;margin-top:6px}
.card .more{color:var(--teal-dark);font-size:12px;font-weight:700;margin-top:6px}

/* about */
.video{left:98px;top:1705px;width:394px;height:208px;background:linear-gradient(120deg,#4a4f56 0%,#6b6660 45%,#8a7f74 70%,#5d6a4a 100%);box-shadow:0 2px 6px rgba(0,0,0,.3)}
.play{left:270px;top:1785px}
.about-title{left:535px;top:1702px;font-size:16.5px;font-weight:500;color:var(--ink);white-space:nowrap}
.about-text{left:535px;top:1736px;width:565px;font-size:11px;line-height:19.5px;color:#555;text-align:justify}
.btn-more{left:535px;top:1877px;width:98px;height:35px;background:var(--teal);color:var(--white);font-size:12px;font-weight:500;text-align:center;line-height:35px;border-radius:2px}

/* footer */
.footer{left:0;top:1956px;width:1200px;height:269px;background:var(--footer)}
.f-col{top:1982px}
.f-col h4{color:var(--white);font-size:14px;font-weight:700;margin-bottom:12px}
.f-col li{list-style:none;color:var(--footer-text);font-size:11.5px;line-height:20px}
.social li{display:flex;align-items:center;gap:12px;line-height:26px}
.social i{width:20px;height:20px;border-radius:50%;display:inline-block}
.f-input{left:854px;width:246px;height:28px;background:#474747;color:#8a8a8a;font-size:11px;line-height:28px;padding:0 8px}
.signup{left:854px;top:2088px;width:67px;height:30px;background:#f2f2f2;color:#555;font-size:11px;font-weight:700;text-align:center;line-height:30px;border-radius:2px}
.f-rule{left:98px;top:2153px;width:1002px;height:1px;background:#3d3d3d}
.copyright{left:98px;top:2180px;color:var(--white);font-size:11.5px}
</style>
</head>
<body>

<div class="abs top-line"></div>

<header>
  <div class="abs brand">
    <span class="brand-mark"></span>
    <span class="brand-name">VILLA RENTAL</span>
  </div>
  <nav class="abs nav">
    <a class="active" href="#">HOME</a><a href="#">LISTING</a><a href="#">AGENTS</a><a href="#">BLOG</a><a href="#">PAGES</a><a href="#">GALLERY</a><a href="#">CONTACTS</a>
  </nav>
</header>

<section>
  <div class="abs hero" role="img" aria-label="Photo of the villa living room with sofa, armchair, dining area and staircase"></div>
  <div class="abs hero-caption">
    <h1>DENOUNCING PLEASURE AND PRAISING</h1>
    <p>Lorem ipsum dolor sit amet, consectetur adipiscing elit, sed do eiusmod tempor incididunt ut labore et dolore magna aliqua. Ut enim ad minim veniam</p>
    <div class="hero-price"><span class="amount">$ 200,00</span><span class="more">VIEW MORE +</span></div>
    <div class="dots"><i></i><i></i><i class="on"></i></div>
  </div>
</section>

<section class="abs search" aria-label="Find your place">
  <div class="abs search-title">FIND YOUR PLACE</div>
  <svg class="abs search-rule" width="250" height="14" viewBox="0 0 250 14">
    <line x1="0" y1="7" x2="112" y2="7" stroke="#fff" stroke-width="1"/>
    <line x1="138" y1="7" x2="250" y2="7" stroke="#fff" stroke-width="1"/>
    <circle cx="124" cy="6" r="4" fill="none" stroke="#fff" stroke-width="1.5"/>
    <line x1="127" y1="9" x2="131" y2="13" stroke="#fff" stroke-width="1.5"/>
  </svg>

  <div class="abs field" style="left:164px;top:97px;width:181px">Location<svg width="10" height="6"><path d="M0 0h10L5 6z" fill="#3aa6c0"/></svg></div>
  <div class="abs field" style="left:363px;top:97px;width:181px">Property type<svg width="10" height="6"><path d="M0 0h10L5 6z" fill="#3aa6c0"/></svg></div>
  <div class="abs field" style="left:562px;top:97px;width:129px">Rooms<svg width="10" height="6"><path d="M0 0h10L5 6z" fill="#3aa6c0"/></svg></div>
  <div class="abs field" style="left:709px;top:97px;width:130px">Beds<svg width="10" height="6"><path d="M0 0h10L5 6z" fill="#3aa6c0"/></svg></div>

  <div class="abs field" style="left:164px;top:157px;width:181px">Features<svg width="10" height="6"><path d="M0 0h10L5 6z" fill="#3aa6c0"/></svg></div>
  <div class="abs field" style="left:363px;top:157px;width:129px">Prices<svg width="10" height="6"><path d="M0 0h10L5 6z" fill="#3aa6c0"/></svg></div>
  <div class="abs field" style="left:510px;top:157px;width:224px">Type any other<svg width="10" height="6"><path d="M0 0h10L5 6z" fill="#3aa6c0"/></svg></div>
  <div class="abs btn-search" style="left:750px;top:157px;width:89px">SEARCH</div>

  <div class="abs btn-book">BOOKING NOW !</div>
</section>

<section>
  <h2 class="abs section-title" style="top:920px">SEASONAL RATES</h2>
  <div class="abs rate-line"></div>
  <div class="abs rate" style="left:98px;top:981px">$ 1,450</div>
  <div class="abs rate" style="left:407px;top:981px">$ 2,450</div>
  <div class="abs rate" style="left:709px;top:981px">$ 3,450</div>
  <div class="abs rate" style="left:1018px;top:981px">$ 4,450</div>
  <div class="abs rate-label" style="left:79px;top:1081px">DIGNISSIMOS</div>
  <div class="abs rate-label" style="left:388px;top:1081px">DIGNISSIMOS</div>
  <div class="abs rate-label" style="left:690px;top:1081px">DIGNISSIMOS</div>
  <div class="abs rate-label" style="left:999px;top:1081px">DIGNISSIMOS</div>
</section>

<section class="abs attractions">
  <h2 class="abs section-title">LOCAL ATTRACTIONS</h2>

  <div class="abs photo" style="left:98px;top:79px;width:206px;height:182px;background:linear-gradient(135deg,#8b8c8e,#cfcac4 60%,#6e6a66)" role="img" aria-label="Photo of a bedroom with artwork and TV"></div>
  <div class="abs card" style="left:304px;top:103px">
    <h3>PRAESENTIUM VOLUPTATUM</h3>
    <p>Must explain to you how all this mistaken idea of and expound the actual teachings of the</p>
    <div class="price">$ 145000</div>
    <div class="more">VIEW MORE+</div>
  </div>

  <div class="abs card" style="left:615px;top:103px">
    <h3>PRAESENTIUM VOLUPTATUM</h3>
    <p>Must explain to you how all this mistaken idea of and expound the actual teachings of the</p>
    <div class="price">$ 145000</div>
    <div class="more">VIEW MORE+</div>
  </div>
  <div class="abs photo" style="left:896px;top:79px;width:206px;height:182px;background:linear-gradient(135deg,#c7c4bd,#9d9488 55%,#5a4f46)" role="img" aria-label="Photo of a lounge with sofa and glass table"></div>

  <div class="abs photo" style="left:98px;top:298px;width:206px;height:183px;background:linear-gradient(135deg,#dcd8d2,#9a8a78 55%,#6a4a34)" role="img" aria-label="Photo of an open living room with wooden floor"></div>
  <div class="abs card" style="left:304px;top:322px">
    <h3>PRAESENTIUM VOLUPTATUM</h3>
    <p>Must explain to you how all this mistaken idea of and expound the actual teachings of the</p>
    <div class="price">$ 145000</div>
    <div class="more">VIEW MORE+</div>
  </div>

  <div class="abs card" style="left:615px;top:322px">
    <h3>PRAESENTIUM VOLUPTATUM</h3>
    <p>Must explain to you how all this mistaken idea of and expound the actual teachings of the</p>
    <div class="price">$ 145000</div>
    <div class="more">VIEW MORE+</div>
  </div>
  <div class="abs photo" style="left:896px;top:298px;width:206px;height:183px;background:linear-gradient(135deg,#3a302c,#6a5e56 50%,#c9c3bd)" role="img" aria-label="Photo of a modern bedroom with dark walls"></div>
</section>

<section>
  <div class="abs video" role="img" aria-label="Walk-through video of the villa exterior and roof"></div>
  <svg class="abs play" width="52" height="52" viewBox="0 0 52 52">
    <circle cx="26" cy="26" r="24" fill="rgba(60,60,60,.75)" stroke="rgba(255,255,255,.4)" stroke-width="2"/>
    <circle cx="26" cy="26" r="15" fill="rgba(120,120,120,.8)"/>
    <path d="M22 18v16l12-8z" fill="#2b2b2b"/>
  </svg>
  <h2 class="abs about-title">ACCUSAMUS ET IUSTO ODIO DIGNISSIMOS DUCIMUS</h2>
  <p class="abs about-text">But I must explain to you how all this mistaken idea of denouncing pleasure and praising pain was born and I will give you a complete account of the system, and expound the actual teachings of the great explorer of the truth, the master-builder of human happiness. No one rejects, dislikes, or avoids pleasure itself, because it is pleasure, but because those who do not know how to pursue pleasure rationally encounter consequences that are extremely painful. Nor again is there anyone who loves or pursues or desires to obtain pain of itself, because it is pain, but because occasionally circumstances</p>
  <div class="abs btn-more">VIEW MORE</div>
</section>

<footer>
  <div class="abs footer"></div>
  <div class="abs f-col" style="left:98px">
    <h4>INFORMATION</h4>
    <ul><li>About us</li><li>Villa concept</li><li>Special areas</li><li>Clients</li><li>Candidates</li><li>Contact us</li></ul>
  </div>
  <div class="abs f-col" style="left:270px">
    <h4>SPECIALIST AREAS</h4>
    <ul><li>Customer Service</li><li>Enim ad minim veniam</li><li>Et aliquipx eato</li><li>Nostrud exercitation</li><li>Affiliates</li></ul>
  </div>
  <div class="abs f-col" style="left:473px">
    <h4>CLIENTS</h4>
    <ul><li>Ut enim&nbsp; minim veniam</li><li>Ullamcode laboris</li><li>Ullamcode laboris</li><li>Et aliquipx eato</li><li>Nostrud exercitation</li></ul>
  </div>
  <div class="abs f-col social" style="left:681px">
    <h4>FOLLOW US</h4>
    <ul>
      <li><i style="background:#3b5a9a"></i>Friendpage</li>
      <li><i style="background:#2aa3e0"></i>Chirper</li>
      <li><i style="background:#d8302a"></i>Vidstream</li>
      <li><i style="background:#dc4a38"></i>Circle Plus</li>
    </ul>
  </div>
  <div class="abs f-col" style="left:854px"><h4>CONTACT US</h4></div>
  <div class="abs f-input" style="top:2017px">your Name</div>
  <div class="abs f-input" style="top:2053px">Enter Your Mail ID</div>
  <div class="abs signup">SIGNUP</div>
  <div class="abs f-rule"></div>
  <div class="abs copyright">Copyright © Villa Rental 2014 .&nbsp; All right reserved.</div>
</footer>

</body>
</html>
```